Creative Fitness Studio Feature Wall

Two feature walls within functional fitness studio, they need to be on brand and have a WOW factor.
Designed to inspire and motivate people to live a fit and healthy lifestyle whilst working out and bringing life to the studio, as an uplifting and inviting environment.

Please see current walls and also visit website www.korvix7.com.au for inspiration.
Updates

Target Market(s)

health and fitness, healthy lifestyle

Industry/Entity Type

Fitness

Font styles to use
Other font styles liked:
• gothic

Colors

Designer to choose colors to be used in the design.

Requirements
Must have
• inspiration from website www.korvix7.com.au ........... brand consistency
Nice to have
• WOW factor......... walk into the gym and it draws your attention.
Should not have
• Overly muscly people (bodybuilders)

```html
<!DOCTYPE html>
<html lang="en">
<head>
<meta charset="utf-8">
<title>Korvix7 Studio Feature Wall</title>
<link href="https://fonts.googleapis.com/css2?family=Crimson+Text:wght@400;600;700&display=swap" rel="stylesheet">
<style>
  :root {
    --wall-dark: #0c1a20;
    --wall-mid: #17323b;
    --wall-teal: #1f4550;
    --brand-green: #7dc243;
    --brand-green-deep: #3f8a2a;
    --text-light: #f2f5f3;
  }
  html, body {
    margin: 0;
    padding: 0;
    width: 1200px;
    height: 774px;
    overflow: hidden;
    background: #e9ecea;
  }
  .feature-wall {
    position: relative;
    width: 1200px;
    height: 774px;
    overflow: hidden;
    background: radial-gradient(ellipse at 45% 35%, var(--wall-teal) 0%, var(--wall-mid) 40%, var(--wall-dark) 85%);
    font-family: "Crimson Text", Georgia, serif;
  }
  .photo-smiling-athlete {
    position: absolute;
    left: 150px;
    top: 90px;
    width: 420px;
    height: 560px;
    background: radial-gradient(ellipse at 50% 40%, rgba(120,150,155,0.45) 0%, rgba(60,90,98,0.3) 45%, rgba(23,50,59,0) 75%);
  }
  .photo-dumbbell-athlete {
    position: absolute;
    left: 700px;
    top: 0;
    width: 440px;
    height: 774px;
    background: linear-gradient(180deg, rgba(20,40,46,0) 0%, rgba(185,140,110,0.55) 25%, rgba(170,125,100,0.6) 45%, rgba(70,170,190,0.5) 55%, rgba(130,110,170,0.5) 75%, rgba(20,40,46,0) 100%);
    -webkit-mask-image: radial-gradient(ellipse 45% 55% at 50% 50%, #000 55%, transparent 100%);
            mask-image: radial-gradient(ellipse 45% 55% at 50% 50%, #000 55%, transparent 100%);
  }
  .swooshes {
    position: absolute;
    left: 0;
    top: 0;
    width: 1200px;
    height: 774px;
  }
  .motto {
    position: absolute;
    left: 60px;
    top: 60px;
    margin: 0;
    padding: 0;
    list-style: none;
  }
  .motto-item { margin-bottom: 26px; }
  .motto-word {
    display: block;
    color: var(--brand-green);
    font-weight: 700;
    font-size: 82px;
    line-height: 0.95;
  }
  .motto-line {
    display: block;
    color: var(--text-light);
    font-weight: 600;
    font-size: 33px;
    line-height: 1.1;
  }
  .brand {
    position: absolute;
    left: 60px;
    top: 615px;
    color: var(--text-light);
  }
  .brand-name {
    display: block;
    font-weight: 700;
    font-size: 72px;
    line-height: 1;
    letter-spacing: 4px;
  }
  .brand-web {
    display: block;
    font-weight: 600;
    font-size: 22px;
    letter-spacing: 1px;
    margin-top: 4px;
  }
</style>
</head>
<body>
<main class="feature-wall">
  <div class="photo-smiling-athlete" role="img" aria-label="Faded photo of a smiling woman training in the gym"></div>
  <div class="photo-dumbbell-athlete" role="img" aria-label="Photo of a fit woman in a blue top curling a dumbbell"></div>

  <svg class="swooshes" viewBox="0 0 1200 774" aria-hidden="true">
    <path d="M0 580 C 250 495, 520 495, 760 580 C 900 630, 1060 615, 1200 555 L 1200 774 L 0 774 Z" fill="var(--wall-dark)" opacity="0.35"/>
    <path d="M0 545 C 220 470, 520 475, 780 580" fill="none" stroke="var(--brand-green)" stroke-width="14"/>
    <path d="M0 575 C 240 505, 520 515, 760 605" fill="none" stroke="var(--brand-green)" stroke-width="6"/>
    <path d="M40 602 C 280 545, 560 560, 800 650" fill="none" stroke="var(--brand-green-deep)" stroke-width="4"/>
    <path d="M520 774 C 780 700, 1000 600, 1200 470 L 1200 774 Z" fill="var(--brand-green)"/>
    <path d="M600 774 C 850 720, 1050 640, 1200 560 L 1200 774 Z" fill="var(--brand-green-deep)" opacity="0.55"/>
    <path d="M700 700 C 900 640, 1060 560, 1200 450" fill="none" stroke="var(--brand-green)" stroke-width="5"/>
  </svg>

  <ul class="motto">
    <li class="motto-item">
      <span class="motto-word">Motivation</span>
      <span class="motto-line">Is What Gets You Started</span>
    </li>
    <li class="motto-item">
      <span class="motto-word">Habit</span>
      <span class="motto-line">Is What Keeps You Going</span>
    </li>
    <li class="motto-item">
      <span class="motto-word">Attitude</span>
      <span class="motto-line">Determines How Well You Do It</span>
    </li>
  </ul>

  <div class="brand">
    <span class="brand-name">KORVIX7</span>
    <span class="brand-web">www.korvix7.com.au</span>
  </div>
</main>
</body>
</html>
```